Web site for small printshop

I am looking for a website for small printshop in Iceland, mainly serving university students and artist.

We print posters, flyers, business cards and more.

In addition to our current website, I would like to include design tool, (fx. www.quarvelpad.example, www.trindomap.example or something similar) jobs upload, shopping chart.
Updates

Great work, I am really amazed of the quality of work i am seeing here.

Really way beyond my expectation

GOOD JOB - all of you ! 

Hi all.

The designs submitted have been great, way better than expected.
I really did not expect this level of quality.

Some have been asking me for feedback on their designs, and I will try 
to send some feedback here, without spoiling your creativity.

Likes:
- when the colors of my logo is used in menus, buttons etc.
- simple, not to crowded look.

Dislikes.
- Dark and heavy design
- Lot of text and buttons (crowded look)

Extra info.
- top line (before menus) will contain: Tel - email - language
- menu line will have 5 categories: Home - service - submission of works - FAQ - about us
- 3 large buttons:  Job submit - Job design - ask for offer

LOVE YOUR WORK - great designs so far :)

Target Market(s)

University Students, Artists. Age group 20-30

Industry/Entity Type

University

Requirements
Must have
• The website must be easy to use, clean looking.

```html
<!DOCTYPE html>
<html lang="en">
<head>
<meta charset="utf-8">
<title>Hverfaprent – Print shop</title>
<link href="https://fonts.googleapis.com/css2?family=Cabin:wght@400;500;600&family=Open+Sans:wght@700&display=swap" rel="stylesheet">
<style>
:root{
  --green:#0e6b3b;
  --green-dark:#0a4f2a;
  --red:#d3261c;
  --yellow:#f1e23a;
  --text:#444;
  --muted:#8a8a8a;
  --line:#e3e3e3;
}
*{box-sizing:border-box;margin:0;padding:0}
html,body{width:1107px;height:1200px;overflow:hidden}
body{position:relative;font-family:'Cabin',sans-serif;color:var(--text);background:#fafafa}
.abs{position:absolute}
.topbar{left:0;top:0;width:1107px;height:6px;background:#3b3b3b}
.header{left:0;top:6px;width:1107px;height:119px;background:linear-gradient(#fff,#f3f3f3)}
.brand{left:92px;top:37px;display:flex;align-items:center;gap:12px}
.brand-mark{width:45px;height:58px;background:var(--red)}
.brand-name{font-family:'Open Sans',sans-serif;font-weight:700;font-size:34px;color:#333;letter-spacing:.5px}
.contact-line{right:91px;top:24px;font-size:19px;color:#666;white-space:nowrap}
.contact-line span{color:var(--red)}
.contact-line .sep{color:#888;margin:0 14px}
.nav{right:91px;top:90px;display:flex;gap:32px;font-size:14px;color:#333}
.nav .active{color:var(--red);position:relative}
.nav .active::after{content:"";position:absolute;left:-4px;right:-4px;top:28px;height:3px;background:var(--red)}
.hero{left:0;top:125px;width:1107px;height:342px;background:linear-gradient(90deg,#e4e4e4,#efefef 45%,#ddd)}
.hero-photo{left:430px;top:125px;width:640px;height:300px;background:linear-gradient(160deg,#bdbdbd,#d8d8d8 45%,#e9c56a 60%,#c86b8a 72%,#8fb5d8 85%,#e8e8e8);opacity:.85;border-radius:0 0 60px 0}
.hero-title{left:92px;top:199px;font-size:27px;line-height:37px;color:var(--green);font-weight:400}
.hero-btn{left:93px;top:321px;width:147px;height:40px;background:var(--green-dark);border-radius:2px;display:flex;align-items:center;gap:9px;padding-left:12px;color:var(--yellow);font-size:20px}
.hero-btn i{width:20px;height:20px;border-radius:50%;background:#062f18;display:block}
.dots{left:94px;top:401px;display:flex;gap:9px}
.dots i{width:13px;height:13px;border-radius:50%;background:#bbb;display:block}
.dots i:first-child{background:#999}
.footer{left:0;top:1080px;width:1107px;height:120px;background:linear-gradient(#2e2e2e,#444)}
.panel{left:91px;top:426px;width:925px;height:681px;background:#fff}
.welcome-title{left:91px;width:925px;top:442px;text-align:center;font-size:25px;color:var(--green);font-weight:400}
.welcome-text{left:120px;width:867px;top:484px;text-align:center;font-size:15px;line-height:25px;color:#555}
.rule{height:1px;background:var(--line);left:110px;width:887px}
.step{top:600px;width:300px}
.step-icon{left:0;top:4px;width:70px;height:70px;border-radius:50%}
.step h3{position:absolute;left:82px;top:0;font-weight:400;font-size:25px;color:var(--muted);white-space:nowrap}
.step h3 span{color:var(--red)}
.step p{position:absolute;left:83px;top:38px;width:210px;font-size:13.5px;line-height:21px;text-align:justify;color:#555}
.section-title{font-size:25px;color:var(--red);font-weight:400}
.services-text{left:104px;top:790px;width:590px;font-size:13.5px;line-height:21px;text-align:justify;color:#555}
.services-text p+p{margin-top:10px}
.service{display:flex;align-items:center;gap:14px;font-size:21px;line-height:27px;color:var(--green)}
.service svg{fill:var(--green);flex:none}
.contact-box{left:721px;top:793px;width:283px;height:285px;background:#e8e8e8;border:1px solid #ccc;border-radius:3px}
.contact-photo{left:730px;top:800px;width:267px;height:141px;background:linear-gradient(#6e7c86 0,#e9e9e9 22%,#dcdcdc 40%,#2f3a40 60%,#4c5358);border:3px solid #fff}
.contact-info{font-size:14px;line-height:21px;color:#444;white-space:nowrap}
.contact-info b{font-weight:600}
.contact-info a{color:var(--red);text-decoration:none}
.footer-nav{left:92px;top:1127px;font-size:14px;color:#ddd}
.footer-nav .sep{margin:0 8px;color:#aaa}
.copyright{left:92px;top:1159px;font-size:14px;color:#ddd;word-spacing:3px}
.social{top:1140px;width:23px;height:23px;border-radius:3px}
</style>
</head>
<body>
<div class="abs topbar"></div>
<header class="abs header"></header>
<div class="abs brand"><div class="brand-mark"></div><div class="brand-name">HVERFAPRENT</div></div>
<div class="abs contact-line">Call us : <span>555 0142</span><span class="sep">|</span>E-mail : <span>verk@hverfa.example</span></div>
<nav class="abs nav"><span class="active">Home</span><span>Services</span><span>Submission of works</span><span>University Printing</span><span>Contact</span></nav>

<section class="abs hero"></section>
<div class="abs hero-photo" role="img" aria-label="Print shop floor with a printing press and colourful calendar sheets"></div>
<h1 class="abs hero-title">We are a small<br>Print company printing<br>Posters, Flyers, Business cards</h1>
<div class="abs hero-btn"><i></i>Contact Us</div>
<div class="abs dots"><i></i><i></i><i></i><i></i></div>

<footer class="abs footer"></footer>

<main class="abs panel"></main>
<h2 class="abs welcome-title">Welcome to Hverfaprent</h2>
<p class="abs welcome-text">Etiam tincidunt venenatis commodo. Maecenas nec mauris facilisis, tincidunt turpis in, dapibus mi. Class aptent taciti sociosqu ad litora torquent per conubia nostra, per inceptos himenaeos. Aliquam dapibus sapien ac egestas congue. Maecenas feugiat risus ac lacus vehicula tincidunt. Praesent ullamcorper blandit enim sed tempus.</p>
<div class="abs rule" style="top:578px"></div>

<div class="abs step" style="left:104px">
  <div class="abs step-icon" role="img" aria-label="Paint palette with brush" style="background:radial-gradient(circle at 40% 40%,#e9c36a,#b88a3a)"></div>
  <h3>Step1 - <span>Create</span></h3>
  <p>Aliquam imperdiet, elit quis tinci dunt eleifend, odio posuere felis, nec suscipit est velit at dui.</p>
</div>
<div class="abs step" style="left:419px">
  <div class="abs step-icon" role="img" aria-label="Upload arrow" style="background:radial-gradient(circle at 40% 40%,#eef3fa,#b9cde8)"></div>
  <h3>Step2 - <span>Upload</span></h3>
  <p>Aliquam imperdiet, elit quis tinci dunt eleifend, odio posuere felis, nec suscipit est velit at dui.</p>
</div>
<div class="abs step" style="left:732px">
  <div class="abs step-icon" role="img" aria-label="Printed photo with magnifier" style="background:radial-gradient(circle at 40% 40%,#e05a4e,#333)"></div>
  <h3>Step3 - <span>Getting</span></h3>
  <p>Aliquam imperdiet, elit quis tinci dunt eleifend, odio posuere felis, nec suscipit est velit at dui.</p>
</div>
<div class="abs rule" style="top:723px"></div>

<h2 class="abs section-title" style="left:103px;top:747px">Our Services</h2>
<div class="abs services-text">
  <p>Nam pretium mauris at turpis malesuada feugiat. Pellentesque et libero consectetur, dictum justo eget, convallis est. Curabitur vel tortor at enim malesuada sollicitudin adipiscing ac magna.</p>
  <p>&nbsp;Fusce adipiscing arcu nec luctus cursus. In eleifend porttitor lorem, quis mattis nisi sodales et. Nulla congue purus et felis pharetra elementum. Integer non suscipit metus, in aliquam orci. Praesent quis tellus non libero sodales convallis. Maecenas vel auctor velit. Quisque pharetra sem eget orci pretium, vitae pretium metus faucibus. Nam ornare neque nec accumsan lobortis.</p>
</div>

<div class="abs service" style="left:136px;top:942px">
  <svg width="48" height="38" viewBox="0 0 48 38"><path d="M14 4h12l3 4h15a3 3 0 0 1 3 3v23a3 3 0 0 1-3 3H4a3 3 0 0 1-3-3V11a3 3 0 0 1 3-3h7zM4 4h7v3H4z"/><circle cx="25" cy="22" r="10" fill="#fff"/><circle cx="25" cy="22" r="6"/></svg>
  <span>General<br>Photocopying</span>
</div>
<div class="abs service" style="left:471px;top:952px">
  <svg width="48" height="42" viewBox="0 0 48 42"><path d="M10 0h28v9H10zM3 11h42a3 3 0 0 1 3 3v15a3 3 0 0 1-3 3h-5V22H8v10H3a3 3 0 0 1-3-3V14a3 3 0 0 1 3-3z"/><path d="M11 25h26v17H11z" fill="none" stroke="#0e6b3b" stroke-width="3"/><path d="M16 31h16M16 36h12" stroke="#0e6b3b" stroke-width="2"/></svg>
  <span>Printing</span>
</div>
<div class="abs service" style="left:134px;top:1028px">
  <svg width="50" height="44" viewBox="0 0 50 44"><path d="M2 6l22 4v34L2 40zM48 6l-22 4v34l22-4z"/></svg>
  <span>Library<br>Printing/Publishing</span>
</div>
<div class="abs service" style="left:474px;top:1036px">
  <svg width="44" height="46" viewBox="0 0 44 46"><path d="M14 0h14v10h10v26H14z"/><path d="M30 0l8 8h-8z"/><path d="M2 14h10v24h16v8H2z"/></svg>
  <span>Scanning / OCR</span>
</div>

<h2 class="abs section-title" style="left:720px;top:747px">Contact us</h2>
<div class="abs contact-box"></div>
<div class="abs contact-photo" role="img" aria-label="Shop front with the company sign above the windows"></div>
<div class="abs contact-info" style="left:735px;top:962px">University Printing<br>Eg: 4 109 - Reykjavik<div style="margin-top:4px">Phone: 555 0142</div><div style="margin-top:4px">verk@hverfa.example</div></div>
<div class="abs contact-info" style="left:881px;top:962px">Opening Hours<br><b>Mon - Fri : 9-17</b><div style="font-size:13px;margin-top:1px">closed on weekends</div><div style="font-size:13px;margin-top:4px"><a>View Location</a></div></div>

<div class="abs footer-nav">Home<span class="sep">|</span>Services<span class="sep">|</span>Submission of works<span class="sep">|</span>University Printing<span class="sep">|</span>Contact</div>
<div class="abs copyright">Copyright © 2013 Hverfaprent. All rights reserved.</div>
<div class="abs social" style="left:965px;background:#3b5a9a"></div>
<div class="abs social" style="left:993px;background:#41b3e6"></div>
</body>
</html>
```